Business card for marketing analytics company

Need a business card for new company. I have a logo already that I want to be built into the card and should use those colours

Company is called steered by tallies
Design must bring steered by tallies to life not be a card that could be for anyone with a logo put on it.

Like the front to be fairly clean and uncluttered bringing the logo out with a suitable design on the back of the card.

The logo represents a compass and business growth so those themes along with numbers, analytics , data are appropriate.
I'm often working with creative industries so also needs to reflect the creative side of analytics rather than be very corporate looking.

Target Market(s)

Ad agency, media agency, consumer goods clients

Industry/Entity Type

Market Research

Contact Information for Business Card

Needs to include name, title, email and phone number

Colors
f78f20
f68d4d
ec1f27

Requirements
Must have
• Must bring steered by tallies to life not be a card that could be for anyone with a logo put on it.
• Logo, Correct colours
• Like a design on the back that relates to company name
• Designs for both sides
Should not have
• Please do not just submit logo and a coloured card.
• It needs to have a design element to it
• No black background
• No clear cards - needs front & back

```html
<!DOCTYPE html>
<html lang="en">
<head>
<meta charset="utf-8">
<title>Steered by Tallies – Business Card</title>
<link href="https://fonts.googleapis.com/css2?family=Figtree:wght@500;600&family=Source+Sans+3:wght@400;600;700&display=swap" rel="stylesheet">
<style>
  :root {
    --backdrop: #000000;
    --card-light: #f3f3f3;
    --card-red: #c12127;
    --card-red-deep: #b11c22;
    --brand-orange: #f78f20;
    --ink-dark: #4b5257;
    --ink-body: #3c3c3c;
    --name-red: #c1272d;
    --white: #ffffff;
  }
  * { box-sizing: border-box; margin: 0; padding: 0; }
  html, body {
    width: 1200px; height: 900px; overflow: hidden;
    background: var(--backdrop);
    font-family: "Source Sans 3", Arial, sans-serif;
  }
  .stage { position: relative; width: 1200px; height: 900px; }

  .card { position: absolute; top: 200px; width: 310px; height: 502px; overflow: hidden; }

  /* Front */
  .card-front {
    left: 265px;
    background: var(--card-light);
    border-radius: 62px 0 62px 0;
  }
  .brand-lockup { position: absolute; left: 22px; top: 58px; display: flex; align-items: center; gap: 20px; }
  .brand-dot { width: 84px; height: 84px; border-radius: 50%; background: var(--brand-orange); }
  .brand-name {
    font-family: "Figtree", Arial, sans-serif;
    color: var(--ink-dark); font-weight: 500; font-size: 26px; line-height: 27px;
  }

  .contact { position: absolute; left: 27px; top: 327px; color: var(--ink-body); }
  .contact-name { color: var(--name-red); font-weight: 600; font-size: 19px; line-height: 22px; }
  .contact-title { font-size: 15px; line-height: 20px; margin-bottom: 15px; }
  .contact-address { font-size: 14.5px; line-height: 16px; margin-bottom: 10px; }
  .contact-line { display: flex; align-items: center; gap: 7px; font-size: 14.5px; line-height: 19px; }
  .contact-line svg { width: 10px; height: 10px; fill: var(--name-red); }

  /* Back */
  .card-back {
    left: 641px;
    background: var(--card-red);
    border-radius: 0 62px 0 62px;
  }
  .back-chart { position: absolute; inset: 0; width: 310px; height: 502px; }
  .back-chart .bar { fill: var(--card-red-deep); }
  .back-chart .grid { stroke: var(--card-red-deep); stroke-width: 3; }
  .back-name {
    position: absolute; left: 30px; top: 388px;
    font-family: "Figtree", Arial, sans-serif;
    color: var(--white); font-weight: 500; font-size: 40px; line-height: 41px;
  }
  .back-name span { display: block; white-space: nowrap; }
  .back-name .second-line { padding-left: 59px; }
</style>
</head>
<body>
<main class="stage">
  <section class="card card-front">
    <div class="brand-lockup">
      <div class="brand-dot"></div>
      <div class="brand-name">Steered by<br>Tallies</div>
    </div>
    <div class="contact">
      <p class="contact-name">ALEX CARTER</p>
      <p class="contact-title">Managing Director</p>
      <p class="contact-address">1234, Address Goes Here<br>Country Name, 123456</p>
      <p class="contact-line">
        <svg viewBox="0 0 10 10" aria-hidden="true"><path d="M1 3.5 C1 1.5 2 1 5 1 C8 1 9 1.5 9 3.5 L7 3.5 L7 2.6 L3 2.6 L3 3.5 Z M2.5 4.5 L7.5 4.5 L9 9 L1 9 Z"/></svg>
        555-204-7311
      </p>
      <p class="contact-line">
        <svg viewBox="0 0 10 10" aria-hidden="true"><path d="M0.5 2 L9.5 2 L9.5 8 L0.5 8 Z M1 2.5 L5 5.5 L9 2.5" stroke="#f3f3f3" stroke-width="0.8"/></svg>
        hello@tallymail.com
      </p>
    </div>
  </section>

  <section class="card card-back">
    <svg class="back-chart" viewBox="0 0 310 502" aria-hidden="true">
      <line class="grid" x1="0" y1="120" x2="310" y2="120"/>
      <line class="grid" x1="0" y1="220" x2="310" y2="220"/>
      <line class="grid" x1="0" y1="320" x2="310" y2="320"/>
      <rect class="bar" x="18"  y="330" width="34" height="172"/>
      <rect class="bar" x="70"  y="270" width="34" height="232"/>
      <rect class="bar" x="122" y="300" width="34" height="202"/>
      <rect class="bar" x="174" y="200" width="34" height="302"/>
      <rect class="bar" x="226" y="140" width="34" height="362"/>
      <rect class="bar" x="278" y="70"  width="34" height="432"/>
    </svg>
    <p class="back-name"><span>Steered by</span><span class="second-line">Tallies</span></p>
  </section>
</main>
</body>
</html>
```